Ashbrook Pit Advertising / Price List

Create a 1 page document for print and email showcasing what we have available in our Quarry. Bottom of sample should have the information included and then the rest of the document focus on items and services available with the quarry. The top section will need room to list about items below and have about 5 pictures that I am working on getting.

Materials Available for Pick Up and/or Delivery:
Recycled Breaker Run
3/4" & 1 1/4" Crushed Recycled Asphalt
1 1/4" Crushed Recycled Stone
1 1/4" Screened "Dig Right On In"
3/4" Clean Stone
3/8" Washed Pea Stone
Mound Sand
Fill Sand Material
Fill/Clay Fill Material
Compost
Peot Moss
Topsoil
Reclaimed Cream City Bricks

Dumping of Materials with Approval:
Clean Concrete
Dirty and / or Large Concrete or Tolvaran
Clean Brick
Asphalt
Fill Material
Brush and / or Stumps
Hydro Vac Slurry Dumping

Target Market(s)

Contractors in our area

Industry/Entity Type

Trucking & Excavation

Colors
EB3D1F
EC4F4E
F09395
F8D3D4
FCEDEE

Requirements
Must have
• Similar Look & Feel as Sample Copy

```html
<!DOCTYPE html>
<html lang="en">
<head>
<meta charset="utf-8">
<title>Ashbrook Pit – Materials &amp; Services</title>
<link href="https://fonts.googleapis.com/css2?family=Rubik:wght@400;500;700&display=swap" rel="stylesheet">
<style>
  :root{
    --red:#E31D25;
    --red-soft:#EC4F4E;
    --pink:#F59A9C;
    --pink-light:#F8D3D4;
    --blush:#FCEDEE;
    --ink:#1E1E1E;
    --white:#FFFFFF;
  }
  html,body{margin:0;padding:0;width:848px;height:1200px;overflow:hidden;background:var(--white);}
  .flyer{position:relative;width:848px;height:1200px;overflow:hidden;font-family:"Rubik",sans-serif;color:var(--ink);background:var(--white);}
  .artwork{position:absolute;inset:0;width:848px;height:1200px;}

  .brand{position:absolute;left:18px;top:92px;color:var(--white);}
  .brand-name{font-weight:700;font-size:30px;letter-spacing:.5px;line-height:1;}
  .brand-tagline{font-weight:500;font-size:5.4px;letter-spacing:.2px;margin-top:5px;}
  .brand-legal{font-weight:700;font-size:8.5px;margin-top:3px;padding-left:14px;}
  .brand-town{font-weight:700;font-size:6.5px;margin-top:2px;padding-left:42px;}

  .section-title{position:absolute;left:337px;margin:0;font-weight:500;font-size:16.5px;color:var(--ink);}
  .materials-title{top:11px;}
  .dumping-title{top:136px;}

  .list{position:absolute;margin:0;padding:0;list-style:none;font-size:10.6px;line-height:12.3px;}
  .list li{position:relative;padding-left:7px;}
  .list li::before{content:"";position:absolute;left:0;top:4.5px;width:3.2px;height:3.2px;border-radius:50%;background:var(--red);}
  .list.spaced li{padding-left:12px;}
  .list.spaced li::before{left:1px;}
  .materials-a{left:337px;top:57px;}
  .materials-b{left:534px;top:57px;}
  .materials-c{left:704px;top:57px;}
  .dumping-a{left:338px;top:163px;font-size:10px;line-height:11.7px;}
  .dumping-b{left:541px;top:163px;font-size:10px;line-height:11.7px;}
  .dumping-c{left:704px;top:163px;font-size:10px;line-height:11.7px;}

  .services-title{position:absolute;left:0;width:848px;top:1074px;margin:0;text-align:center;font-weight:700;font-size:21.5px;color:var(--pink-light);padding-left:18px;box-sizing:border-box;}
  .service{position:absolute;top:1104px;margin:0;text-align:center;font-weight:700;font-size:18px;line-height:17px;color:var(--pink-light);transform:translateX(-50%);white-space:nowrap;}
  .service.brush{left:124px;}
  .service.excavating{left:328px;}
  .service.snow{left:536px;}
  .service.trucking{left:732px;}

  .contact-bar{position:absolute;left:0;top:1158px;width:848px;height:42px;background:var(--pink);}
  .contact{position:absolute;top:6px;display:flex;align-items:center;gap:6px;font-weight:700;font-size:12.6px;line-height:14px;color:#3A0C0E;}
  .contact svg{flex:none;fill:#3A0C0E;}
  .contact.address{left:37px;}
  .contact.online{left:262px;}
  .contact.phone{left:548px;}
  .contact.phone .lines{margin-left:6px;}
  .line-item{display:flex;align-items:center;gap:5px;}
</style>
</head>
<body>
<div class="flyer">
  <svg class="artwork" viewBox="0 0 848 1200" aria-hidden="false">
    <defs>
      <linearGradient id="yardGradient" x1="0" y1="0" x2="0" y2="1">
        <stop offset="0" stop-color="#8FB8E4"/>
        <stop offset="0.22" stop-color="#7E7466"/>
        <stop offset="0.34" stop-color="#4E6F96"/>
        <stop offset="0.5" stop-color="#C9362E"/>
        <stop offset="0.75" stop-color="#C24A42"/>
        <stop offset="1" stop-color="#CFC6B8"/>
      </linearGradient>
      <linearGradient id="demolitionGradient" x1="0" y1="0" x2="0" y2="1">
        <stop offset="0" stop-color="#5A4A40"/><stop offset="0.5" stop-color="#B89A3A"/><stop offset="1" stop-color="#8C8278"/>
      </linearGradient>
      <linearGradient id="excavationGradient" x1="0" y1="0" x2="0" y2="1">
        <stop offset="0" stop-color="#7FB2E6"/><stop offset="0.5" stop-color="#C7B34A"/><stop offset="1" stop-color="#6A4A34"/>
      </linearGradient>
      <linearGradient id="snowGradient" x1="0" y1="0" x2="0" y2="1">
        <stop offset="0" stop-color="#C9CDD2"/><stop offset="0.45" stop-color="#8E8A70"/><stop offset="1" stop-color="#F4F5F7"/>
      </linearGradient>
      <linearGradient id="interiorGradient" x1="0" y1="0" x2="0" y2="1">
        <stop offset="0" stop-color="#9A9A98"/><stop offset="0.5" stop-color="#6F7C86"/><stop offset="1" stop-color="#8A6E58"/>
      </linearGradient>
    </defs>

    <!-- top-left brand swoosh -->
    <path fill="var(--red)" d="M0,0 L320,0 C270,110 160,190 0,199 Z"/>

    <!-- photo frame dividers -->
    <g stroke="var(--red)" stroke-width="1.2">
      <line x1="154" y1="246" x2="154" y2="338"/>
      <line x1="335" y1="246" x2="335" y2="338"/>
      <line x1="521" y1="246" x2="521" y2="338"/>
      <line x1="697" y1="246" x2="697" y2="338"/>
    </g>

    <!-- middle red wave band -->
    <path fill="var(--red)" d="M0,414 C60,440 150,470 240,455 C360,432 460,360 590,352 C700,348 790,370 848,395 L848,460 L0,520 Z"/>
    <path fill="var(--white)" d="M0,470 C100,520 250,500 310,410 C250,470 120,480 0,445 Z"/>

    <!-- yard photograph -->
    <path role="img" aria-label="Photo: red roll-off trucks and dumpsters lined up in the quarry yard beside a river"
          fill="url(#yardGradient)"
          d="M0,498 C120,520 260,505 380,460 C470,425 540,400 620,397 C720,394 800,410 848,430 L848,1000 L0,1000 Z"/>
    <path fill="var(--white)" d="M0,498 C120,520 260,505 380,460 C270,490 120,500 0,470 Z"/>

    <!-- bottom red area -->
    <path fill="var(--red)" d="M0,1000 L0,925 C140,900 260,880 400,840 C520,810 640,800 720,812 C790,822 830,850 848,880 L848,1200 L0,1200 Z"/>
    <path fill="var(--white)" d="M0,900 C60,945 170,960 260,930 C170,940 60,920 0,875 Z"/>
    <path fill="var(--white)" d="M400,860 C520,812 680,805 848,890 L848,905 C700,830 540,830 400,860 Z"/>

    <!-- service circles -->
    <g stroke="var(--white)" stroke-width="5">
      <circle cx="126" cy="983" r="78" fill="url(#demolitionGradient)" role="img" aria-label="Photo: yellow excavator demolishing a brick building"/>
      <circle cx="328" cy="983" r="78" fill="url(#excavationGradient)" role="img" aria-label="Photo: excavator digging soil on a job site"/>
      <circle cx="530" cy="983" r="78" fill="url(#snowGradient)" role="img" aria-label="Photo: loaders clearing snow from a parking lot"/>
      <circle cx="731" cy="983" r="78" fill="url(#interiorGradient)" role="img" aria-label="Photo: excavator clearing debris inside a large hall"/>
    </g>
  </svg>

  <div class="brand">
    <div class="brand-name">ASHBROOK PIT</div>
    <div class="brand-tagline">BRUSH CUTTING . EXCAVATING . SNOW REMOVAL . TRUCKING</div>
    <div class="brand-legal">ASHBROOK PIT, LLC</div>
    <div class="brand-town">HARLOW FALLS, WI</div>
  </div>

  <h2 class="section-title materials-title">Materials Available for Pick Up and/or Delivery:</h2>
  <ul class="list materials-a">
    <li>Recycled Breaker Run</li>
    <li>3/4" &amp; 1 1/4" Crushed<br>Recycled Asphalt</li>
    <li>1 1/4" Crushed Recycled Stone</li>
    <li>1 1/4" Screened "Dig Right<br>On In"</li>
  </ul>
  <ul class="list spaced materials-b">
    <li>3/4" Clean Stone</li>
    <li>3/8" Washed Pea Stone</li>
    <li>Mound Sand</li>
    <li>Fill Sand Material</li>
    <li>Fill/Clay Fill Material</li>
  </ul>
  <ul class="list spaced materials-c">
    <li>Compost</li>
    <li>Peot Moss</li>
    <li>Topsoil</li>
    <li>Reclaimed Cream<br>City Bricks</li>
  </ul>

  <h2 class="section-title dumping-title">Dumping of Materials with Approval:</h2>
  <ul class="list dumping-a">
    <li>Clean Concrete</li>
    <li>Dirty and / or Large Concrete<br>or Tolvaran</li>
  </ul>
  <ul class="list dumping-b">
    <li>Clean Brick</li>
    <li>Asphalt</li>
    <li>Fill Material</li>
  </ul>
  <ul class="list spaced dumping-c">
    <li>Brush and / or Stumps</li>
    <li>Hydro Vac Slurry</li>
    <li>Dumping</li>
  </ul>

  <h2 class="services-title">Our Commercial and Residential Services Include</h2>
  <p class="service brush">Brush Cutting</p>
  <p class="service excavating">Excavating</p>
  <p class="service snow">Snow Plowing and<br>Removal</p>
  <p class="service trucking">Trucking</p>

  <footer class="contact-bar">
    <div class="contact address">
      <svg width="11" height="15" viewBox="0 0 12 16"><path d="M6,0 C2.7,0 0,2.6 0,5.8 C0,10 6,16 6,16 C6,16 12,10 12,5.8 C12,2.6 9.3,0 6,0 Z M6,8.2 A2.4,2.4 0 1 1 6,3.4 A2.4,2.4 0 1 1 6,8.2 Z"/></svg>
      <div>1480 Quarry Ridge Road<br>Harlow Falls, WI 54099</div>
    </div>
    <div class="contact online">
      <div>
        <div class="line-item"><svg width="12" height="9" viewBox="0 0 12 9"><path d="M0,0 H12 V9 H0 Z M1,1 L6,5 L11,1 Z" fill-rule="evenodd"/></svg>dispatch@ashbrookpitllc.com</div>
        <div class="line-item"><svg width="12" height="12" viewBox="0 0 12 12"><circle cx="6" cy="6" r="5.3" fill="none" stroke="#3A0C0E" stroke-width="1"/><ellipse cx="6" cy="6" rx="2.4" ry="5.3" fill="none" stroke="#3A0C0E" stroke-width="1"/><line x1="0.7" y1="6" x2="11.3" y2="6" stroke="#3A0C0E" stroke-width="1"/></svg>www.ashbrookpitllc.com</div>
      </div>
    </div>
    <div class="contact phone">
      <svg width="15" height="18" viewBox="0 0 16 18"><path d="M3.5,0.5 L6,4.5 L4.3,6.3 C5.2,8.8 7,11 9.6,12.6 L11.4,11 L15.5,13.6 L13.6,17 C6.5,16.5 0.8,9.8 0.5,2.3 Z"/></svg>
      <div class="lines">Call or Text 555-014-2287<br>Fax 555-014-2288</div>
    </div>
  </footer>
</div>
</body>
</html>
```